Need Business Card ASAP

We need a business card design for a meeting coming up in a few days. The company name is Harlow Ridge Building and Construction and the logo is attached. Something clean, cool, and contemporary that we can get to a printer right away. Attached is the business card for Volmar Energy, an affiliated company, which we like. Instead of the hawk on the back, you could use the attached "D". We'll also be needing matching letterhead in the near future, so ideas for that are welcome.

```html
<!DOCTYPE html>
<html lang="en">
<head>
<meta charset="utf-8">
<title>Harlow Ridge Building and Construction – Business Card</title>
<link rel="stylesheet" href="https://fonts.googleapis.com/css2?family=Open+Sans:wght@400;600;700&family=Arimo:wght@400;700&display=swap">
<style>
  :root {
    --page: #e9e7e2;
    --card-white: #ffffff;
    --khaki: #c8c397;
    --khaki-deep: #b9b283;
    --khaki-light: #e6e2cf;
    --khaki-text: #bdb78a;
    --ink: #231f20;
    --ink-soft: #4a4a4a;
    --on-dark: #ffffff;
  }
  * { box-sizing: border-box; margin: 0; padding: 0; }
  html, body { width: 1034px; height: 1200px; overflow: hidden; }
  body { background: var(--page); position: relative; font-family: "Open Sans", Arial, sans-serif; }

  .card {
    position: absolute;
    left: 73px;
    width: 888px;
    height: 507px;
    box-shadow: 0 2px 8px rgba(0,0,0,0.18);
  }
  .card--front { top: 56px; background: var(--card-white); }
  .card--back { top: 610px; background: var(--khaki); }

  /* Front: brand block */
  .brand-block { position: absolute; left: 90px; top: 59px; width: 230px; height: 295px; }
  .brand-block__field {
    height: 181px;
    background: linear-gradient(135deg, var(--khaki-deep) 0%, var(--khaki) 45%, var(--khaki-light) 100%);
  }
  .brand-block__band {
    height: 114px;
    background: var(--ink);
    display: flex; align-items: center; justify-content: center;
  }
  .brand-block__name {
    color: var(--on-dark);
    font-family: "Open Sans", Arial, sans-serif;
    font-weight: 600;
    font-size: 27px;
    letter-spacing: 0.5px;
  }

  /* Front: contact panel */
  .contact-panel {
    position: absolute; left: 456px; top: 57px; width: 432px; height: 301px;
    background: linear-gradient(180deg, var(--khaki) 0%, var(--khaki-light) 100%);
    padding: 20px 0 0 36px;
    color: var(--ink);
  }
  .contact-panel__name { font-family: "Open Sans", Arial, sans-serif; font-weight: 700; font-size: 31px; line-height: 1.1; }
  .contact-panel__title { font-family: "Open Sans", Arial, sans-serif; font-weight: 600; font-size: 20px; margin-top: 4px; }
  .contact-list { list-style: none; margin-top: 20px; font-family: "Arimo", Arial, sans-serif; font-size: 23px; }
  .contact-list li { display: flex; align-items: center; height: 44px; }
  .contact-list svg { width: 18px; height: 18px; margin-right: 12px; fill: var(--ink); flex: none; }

  .company-line {
    position: absolute; left: 0; right: 0; top: 414px; text-align: center;
    color: var(--khaki-text); font-weight: 600; font-size: 28px; letter-spacing: 0.3px;
  }
  .address-line {
    position: absolute; left: 0; right: 0; top: 456px; text-align: center;
    color: var(--ink); font-size: 21px;
  }

  /* Back */
  .back-brand {
    position: absolute; left: 90px; top: 200px;
    color: var(--card-white); font-weight: 600; font-size: 44px; letter-spacing: 0.5px;
  }
  .back-web {
    position: absolute; left: 456px; top: 234px;
    font-family: "Arimo", Arial, sans-serif; font-weight: 700; font-size: 25px; color: var(--ink-soft);
  }
</style>
</head>
<body>

<section class="card card--front" aria-label="Business card front">
  <div class="brand-block">
    <div class="brand-block__field"></div>
    <div class="brand-block__band"><span class="brand-block__name">Harlow Ridge</span></div>
  </div>

  <div class="contact-panel">
    <p class="contact-panel__name">Your Name</p>
    <p class="contact-panel__title">Title</p>
    <ul class="contact-list">
      <li>
        <svg viewBox="0 0 24 24" aria-hidden="true"><path d="M6.6 10.8a15.1 15.1 0 0 0 6.6 6.6l2.2-2.2c.3-.3.7-.4 1-.2 1.1.4 2.3.6 3.6.6.6 0 1 .4 1 1V20c0 .6-.4 1-1 1A17 17 0 0 1 3 4c0-.6.4-1 1-1h3.5c.6 0 1 .4 1 1 0 1.3.2 2.5.6 3.6.1.3 0 .7-.2 1z"/></svg>
        (123) 456-7890
      </li>
      <li>
        <svg viewBox="0 0 24 24" aria-hidden="true"><path d="M8 1h8a2 2 0 0 1 2 2v18a2 2 0 0 1-2 2H8a2 2 0 0 1-2-2V3a2 2 0 0 1 2-2zm0 3v13h8V4zm4 15a1.2 1.2 0 1 0 0 2.4 1.2 1.2 0 0 0 0-2.4z"/></svg>
        (123) 456-7890
      </li>
      <li>
        <svg viewBox="0 0 24 24" aria-hidden="true"><path d="M2 6l10 6 10-6v12H2zm0-2h20l-10 6z"/></svg>
        yourname@harlowridge.com
      </li>
      <li>
        <svg viewBox="0 0 24 24" aria-hidden="true"><path d="M12 2a10 10 0 1 0 0 20 10 10 0 0 0 0-20zm6.9 9h-3a15 15 0 0 0-1.3-6A8 8 0 0 1 18.9 11zM12 4.1c.9 1.3 1.7 3.8 1.9 6.9h-3.8c.2-3.1 1-5.6 1.9-6.9zM9.4 5a15 15 0 0 0-1.3 6h-3A8 8 0 0 1 9.4 5zM5.1 13h3a15 15 0 0 0 1.3 6A8 8 0 0 1 5.1 13zm6.9 6.9c-.9-1.3-1.7-3.8-1.9-6.9h3.8c-.2 3.1-1 5.6-1.9 6.9zm2.6-.9a15 15 0 0 0 1.3-6h3a8 8 0 0 1-4.3 6z"/></svg>
        www.harlowridge.com
      </li>
    </ul>
  </div>

  <p class="company-line">HARLOW RIDGE BUILDING &amp; CONSTRUCTION</p>
  <p class="address-line">00, Complex Name, Street, City 00000</p>
</section>

<section class="card card--back" aria-label="Business card back">
  <p class="back-brand">Harlow Ridge</p>
  <p class="back-web">www.harlowridgebuilding.com</p>
</section>

</body>
</html>
```